Home Fund Guide

Have clients check their mortgage qualifications before they go looking for a mortgage lender. This program gains access to your lenders credit report / 3 scores without impacting your credit scores.

```html
<!DOCTYPE html>
<html lang="en">
<head>
<meta charset="UTF-8">
<title>Home Fund Guide – Business Card</title>
<link href="https://fonts.googleapis.com/css2?family=Montserrat:wght@600;700&family=Roboto:wght@400;500&display=swap" rel="stylesheet">
<style>
  :root {
    --backdrop: #d9d9db;
    --card-white: #ffffff;
    --brand-blue: #0442c6;
    --brand-blue-light: #0a5cd0;
    --brand-green: #06c46e;
    --text-dark: #2b2b2b;
    --card-shadow: 0 18px 40px rgba(0, 0, 0, 0.22);
  }
  * { box-sizing: border-box; margin: 0; padding: 0; }
  html, body {
    width: 1200px;
    height: 800px;
    overflow: hidden;
  }
  body {
    background: var(--backdrop);
    display: flex;
    align-items: center;
    justify-content: center;
    gap: 40px;
  }
  .card {
    width: 540px;
    height: 310px;
    border-radius: 26px;
    box-shadow: var(--card-shadow);
    position: relative;
    overflow: hidden;
  }

  /* Front side */
  .card--front { background: var(--card-white); }
  .front-details {
    position: absolute;
    left: 34px;
    top: 40px;
    width: 260px;
  }
  .brand-name {
    font-family: "Montserrat", sans-serif;
    font-weight: 600;
    font-size: 24px;
    color: var(--brand-blue);
    letter-spacing: 0.2px;
    margin-bottom: 22px;
  }
  .person-name {
    font-family: "Montserrat", sans-serif;
    font-weight: 700;
    font-size: 19px;
    color: var(--brand-blue);
    line-height: 1.1;
  }
  .person-title {
    font-family: "Montserrat", sans-serif;
    font-weight: 600;
    font-size: 12px;
    color: var(--brand-green);
    margin-bottom: 14px;
  }
  .address {
    font-family: "Roboto", sans-serif;
    font-size: 11.5px;
    color: var(--text-dark);
    line-height: 1.4;
    margin-bottom: 10px;
  }
  .contact-list { list-style: none; }
  .contact-item {
    font-family: "Roboto", sans-serif;
    font-size: 11.5px;
    color: var(--text-dark);
    line-height: 1.5;
    display: flex;
    align-items: center;
    gap: 8px;
  }
  .contact-icon {
    width: 11px;
    height: 11px;
    flex: none;
    fill: var(--brand-green);
  }
  .front-mark {
    position: absolute;
    right: 28px;
    top: 28px;
    width: 200px;
    height: 200px;
    border-radius: 34px;
    background: linear-gradient(135deg, var(--brand-blue), var(--brand-blue-light));
  }

  /* Back side */
  .card--back {
    background: var(--brand-blue);
    display: flex;
    flex-direction: column;
    align-items: center;
    justify-content: center;
    gap: 22px;
  }
  .back-mark {
    width: 70px;
    height: 70px;
    border-radius: 12px;
    background: var(--card-white);
  }
  .back-brand-name {
    font-family: "Montserrat", sans-serif;
    font-weight: 600;
    font-size: 34px;
    color: var(--card-white);
    letter-spacing: 0.3px;
  }
</style>
</head>
<body>

  <section class="card card--front" aria-label="Business card front">
    <div class="front-details">
      <div class="brand-name">Home Fund Guide</div>
      <div class="person-name">Daniel Carter</div>
      <div class="person-title">President</div>
      <p class="address">4210 Maple Ridge Road<br>Boise, Idaho 83702</p>
      <ul class="contact-list">
        <li class="contact-item">
          <svg class="contact-icon" viewBox="0 0 24 24" aria-hidden="true"><path d="M6.6 10.8a15 15 0 0 0 6.6 6.6l2.2-2.2c.3-.3.7-.4 1-.2 1.1.4 2.3.6 3.6.6.6 0 1 .4 1 1V20c0 .6-.4 1-1 1A17 17 0 0 1 3 4c0-.6.4-1 1-1h3.5c.6 0 1 .4 1 1 0 1.3.2 2.5.6 3.6.1.3 0 .7-.2 1z"/></svg>
          555-214-7360
        </li>
        <li class="contact-item">
          <svg class="contact-icon" viewBox="0 0 24 24" aria-hidden="true"><path d="M7 2h10a2 2 0 0 1 2 2v16a2 2 0 0 1-2 2H7a2 2 0 0 1-2-2V4a2 2 0 0 1 2-2zm0 3v13h10V5z"/></svg>
          555-318-4092
        </li>
        <li class="contact-item">
          <svg class="contact-icon" viewBox="0 0 24 24" aria-hidden="true"><path d="M4 4h16a2 2 0 0 1 2 2v3H2V6a2 2 0 0 1 2-2zm-2 7h20v7a2 2 0 0 1-2 2H4a2 2 0 0 1-2-2zm4 3v2h6v-2z"/></svg>
          555-427-1185
        </li>
        <li class="contact-item">
          <svg class="contact-icon" viewBox="0 0 24 24" aria-hidden="true"><path d="M2 5h20v14H2zm2 2v.5l8 5 8-5V7z"/></svg>
          info@homefundguide.com
        </li>
        <li class="contact-item">
          <svg class="contact-icon" viewBox="0 0 24 24" aria-hidden="true"><circle cx="12" cy="12" r="10"/></svg>
          homefundguide.com
        </li>
      </ul>
    </div>
    <div class="front-mark" aria-hidden="true"></div>
  </section>

  <section class="card card--back" aria-label="Business card back">
    <div class="back-mark" aria-hidden="true"></div>
    <div class="back-brand-name">Home Fund Guide</div>
  </section>

</body>
</html>
```